Business Card Design Project for a Restaurant/Wine Bar

New, fresh business card design for Brevenna Wine Bar & Restaurant, Bandon, Oregon. We are an established restaurant on the Oregon coast featuring "Italian coastal cuisine."

"Brevenna" means bay leaf in Italian. We aren't sure if we would like our logo on the card or not, but if you have something interesting that uses it, then please do so. The basic information is essential - full restaurant name, address, phone and website (do not use www). The font on our menu and wine list may give you some sort of an idea of our style.

One-sided card needed as we often use the backside to write down various types of info for customers.
Updates

After seeing a few submissions, we would like to see what designers can come up with-using the logo, just the leaf, or none at all. Sky is the limit as long as our full restaurant name, address, phone and website (please leave out www) are there. Please contact us if questions!

I appreciate all of your designs! Our deadline is next week, but I will continue to give feedback on designs as I can. This is our busiest season, so my co-owner/chef/husband, won't have time to look at the designs for awhile. When he does, we can make our decision.

cheers,
Maren

Target Market(s)

Fine dining/wine crowd. Would like something simple and elegant, but not pretentious or stuffy. Brevenna means bay laurel (bay leaf) in Italian (please see our logo).

Industry/Entity Type

Restaurant

Requirements
Must have
• Full Name of Restaurant: Brevenna Wine Bar & Restaurant
Address: 812 4th Ave NW, Bandon, Oregon 97411
Phone: 541.555.0172
website: brevennawinebar.example (do not use www)
Should not have
• Loud colors.

```html
<!DOCTYPE html>
<html lang="en">
<head>
<meta charset="utf-8">
<title>Brevenna Wine Bar & Restaurant – Business Card</title>
<link rel="stylesheet" href="https://fonts.googleapis.com/css2?family=Noto+Serif:wght@400;700&family=Italianno&family=Caveat:wght@500&display=swap">
<style>
  :root {
    --page: #ffffff;
    --paper: #c2b58f;
    --paper-light: #cbbf9c;
    --band: #c98a45;
    --band-text: #f4e79a;
    --night: #161616;
    --night-edge: #202020;
    --gold: #f5b400;
    --white: #ffffff;
    --brown: #4a2e14;
    --rule: #6b5a3a;
    --serif: "Noto Serif", Georgia, serif;
    --script: "Italianno", cursive;
    --hand: "Caveat", cursive;
  }
  * { margin: 0; padding: 0; box-sizing: border-box; }
  html, body { width: 1200px; height: 900px; overflow: hidden; background: var(--page); }
  .canvas { position: relative; width: 1200px; height: 900px; }

  .card { position: absolute; width: 506px; height: 824px; overflow: hidden; }
  .card--front { left: 55px; top: 44px; }
  .card--back { left: 637px; top: 42px; background: radial-gradient(ellipse at 40% 40%, var(--paper-light), var(--paper)); border: 1px solid #b3a680; }

  .front__paper { position: absolute; left: 0; top: 0; width: 100%; height: 432px; background: radial-gradient(ellipse at 45% 40%, var(--paper-light), var(--paper)); }
  .front__band { position: absolute; left: 0; top: 432px; width: 100%; height: 86px; background: var(--band); display: flex; align-items: center; justify-content: center; }
  .tagline { font-family: var(--script); font-size: 46px; color: var(--band-text); letter-spacing: 2px; }
  .front__dark { position: absolute; left: 0; top: 518px; width: 100%; height: 306px; background: linear-gradient(180deg, var(--night-edge), var(--night)); text-align: center; font-family: var(--serif); color: var(--white); }

  .brand-mark { position: absolute; left: 0; width: 100%; text-align: center; font-family: var(--serif); font-weight: 700; color: var(--brown); line-height: 1.1; }
  .card--front .brand-mark { top: 168px; font-size: 50px; }
  .card--back .brand-mark { top: 560px; font-size: 28px; }

  .name { margin-top: 42px; font-size: 64px; font-weight: 700; color: var(--gold); line-height: 1; }
  .subname { font-size: 23px; margin-top: 4px; }
  .address { font-size: 20px; font-weight: 700; margin-top: 26px; }
  .phone { font-size: 20px; font-weight: 700; color: var(--band); margin-top: 6px; }
  .web { font-size: 20px; font-weight: 700; margin-top: 6px; }

  .notes { position: absolute; left: 34px; top: 121px; width: 432px; }
  .notes__line { height: 66px; border-bottom: 1px solid var(--rule); }
  .notes__line:first-child { height: 0; }

  .back__name { position: absolute; left: 0; top: 676px; width: 100%; text-align: center; font-family: var(--serif); font-weight: 700; font-size: 21px; color: var(--brown); }
  .back__details { position: absolute; left: 0; top: 706px; width: 100%; text-align: center; font-family: var(--hand); font-size: 19px; line-height: 22px; color: var(--brown); }
</style>
</head>
<body>
<div class="canvas">
  <section class="card card--front">
    <div class="front__paper"></div>
    <div class="brand-mark">Brevenna<br>Wine Bar</div>
    <div class="front__band"><p class="tagline">Italian Coastal Cuisine</p></div>
    <div class="front__dark">
      <p class="name">Brevenna</p>
      <p class="subname">Wine Bar &amp; Restaurant</p>
      <p class="address">812 4th Avenue NW, Bandon, Oregon 97411</p>
      <p class="phone">(541) 555-0172</p>
      <p class="web">brevennawinebar.example</p>
    </div>
  </section>

  <section class="card card--back">
    <div class="notes">
      <div class="notes__line"></div>
      <div class="notes__line"></div>
      <div class="notes__line"></div>
      <div class="notes__line"></div>
      <div class="notes__line"></div>
      <div class="notes__line"></div>
    </div>
    <div class="brand-mark">Brevenna<br>Wine Bar</div>
    <p class="back__name">BREVENNA WINE BAR &amp; RESTAURANT</p>
    <div class="back__details">
      <p>Address: 812 4th Avenue NW, Bandon, Oregon 97411</p>
      <p>Phone: (541) 555-0172</p>
      <p>Email: brevennawinebar.example</p>
    </div>
  </section>
</div>
</body>
</html>
```